Upmarket Dessert Lounge needs a Business Card Design

We are an upmarket dessert lounge needing a business card to match our image.

We want something that is simple yet beautiful, feminine, classy, sophisticated and elegant. We want it to stand out and don't mind if it is bold.

The design should include our logo and colours of red or maroon with gold highlights. We don't mind if black is used.

Marlow & Quince

Target Market(s)

For those who like to indulge or treat themselves and give in to their temptations on good quality desserts.

Industry/Entity Type

Business

Requirements
Must have
• Must include our logo and our name

Marlow & Quince

M & Q

```html
<!DOCTYPE html>
<html lang="en">
<head>
<meta charset="utf-8">
<title>Marlow &amp; Quince — Business Card</title>
<link rel="stylesheet" href="https://fonts.googleapis.com/css2?family=Source+Sans+3:wght@400;600;700&display=swap">
<style>
  :root {
    --maroon: #7a1416;
    --gold: #c9a24a;
    --gold-light: #f6d9a6;
    --paper: #ffffff;
    --ink: #333333;
    --ink-soft: #444444;
    --backdrop: #d9d9d9;
  }
  * { margin: 0; padding: 0; box-sizing: border-box; }
  html, body { width: 956px; height: 1200px; overflow: hidden; }
  body {
    background: var(--backdrop);
    font-family: "Source Sans 3", "Myriad Pro", Arial, sans-serif;
    position: relative;
  }
  .card {
    position: absolute;
    background: var(--paper);
    border-radius: 28px;
    overflow: hidden;
    box-shadow: 0 6px 14px rgba(0,0,0,0.25);
  }
  .card--front { left: 78px; top: 96px; width: 799px; height: 456px; }
  .card--back  { left: 74px; top: 632px; width: 798px; height: 456px; }

  .swoosh { position: absolute; inset: 0; width: 100%; height: 100%; }

  .brand {
    position: absolute;
    left: 58px; top: 112px;
    width: 376px;
    display: flex;
    align-items: center;
    justify-content: center;
    gap: 14px;
  }
  .brand__dot {
    width: 16px; height: 16px;
    border-radius: 50%;
    background: var(--gold);
    flex: none;
  }
  .brand__name {
    color: var(--maroon);
    font-weight: 400;
    font-size: 36px;
    line-height: 1;
    letter-spacing: 1.5px;
    text-transform: uppercase;
    white-space: nowrap;
  }

  .monogram {
    position: absolute;
    inset: 0;
    display: flex;
    align-items: center;
    justify-content: center;
    gap: 24px;
  }
  .monogram__dot {
    width: 26px; height: 26px;
    border-radius: 50%;
    background: var(--gold);
  }
  .monogram__letters {
    color: var(--maroon);
    font-weight: 400;
    font-size: 108px;
    line-height: 1;
    letter-spacing: 2px;
  }

  .person { position: absolute; left: 60px; top: 279px; color: var(--ink); }
  .person__name { font-weight: 700; font-size: 24px; line-height: 30px; }
  .person__role { font-size: 24px; line-height: 30px; color: var(--ink-soft); letter-spacing: 0.5px; }

  .contact-list {
    position: absolute;
    list-style: none;
    font-size: 20px;
    line-height: 27px;
    color: var(--ink);
  }
  .contact-list b { font-weight: 700; }
  .contact-list--phones { left: 64px; top: 354px; }
  .contact-list--web { left: 277px; top: 309px; }
  .address {
    position: absolute; left: 279px; top: 380px;
    font-style: normal; font-size: 20px; line-height: 27px; color: var(--ink);
  }
</style>
</head>
<body>
  <section class="card card--front">
    <svg class="swoosh" viewBox="0 0 799 456" aria-hidden="true">
      <path fill="var(--maroon)" d="M550,0 C720,40 790,250 672,456 L799,456 L799,0 Z"/>
      <path fill="var(--paper)" d="M650,0 C725,45 765,170 737,372 C775,230 762,80 692,0 Z"/>
    </svg>
    <div class="brand">
      <span class="brand__dot"></span>
      <span class="brand__name">Marlow &amp; Quince</span>
    </div>
    <div class="person">
      <div class="person__name">Your Name</div>
      <div class="person__role">Designation</div>
    </div>
    <ul class="contact-list contact-list--phones">
      <li><b>p</b> : 123-456-7890</li>
      <li><b>c</b> : 123-456-7890</li>
      <li><b>f</b> : 123-456-7890</li>
    </ul>
    <ul class="contact-list contact-list--web">
      <li><b>e</b> : name@yourwebsite.com</li>
      <li><b>w</b> : www.marlow&amp;quince.com</li>
    </ul>
    <address class="address">0000, Street Name<br>City Name, Country Code.</address>
  </section>

  <section class="card card--back">
    <div class="monogram">
      <span class="monogram__dot"></span>
      <span class="monogram__letters">M &amp; Q</span>
    </div>
  </section>
</body>
</html>
```